CBD AgriBusiness Verdant Trophy Business Card

We are HiTec producer of medical cannabis CBD Switzerland of high quality. Our website is alpinleaf.net, we will also revisit it graphically, the winner of this contest will be the graphic designer chosen for the new design of the website. We stand out by the skill of the team, many of our engineers we win cup cannabis. I join the current map to take as an example but to revisit completely: deletion of surname and first name, modification of funds (front / back), reorganization of text info, highlighting the address of the website. three characteristics define the business card: Professional, Class, refined. The business card must be optimized for soft-touch and selective varnish printing.

Target Market(s)

Customers and Suppliers

Industry/Entity Type

Agribusiness

Contact Information for Business Card

Logo, Tél / Whatsapp, mail, url du site : alpinleaf.net

Font styles to use
Sans Serif

Requirements
Must have
• Logo of alpinleaf.net
Nice to have
• a design that stands out well on the selective varnish
Should not have
• Last name and first name

```html
<!DOCTYPE html>
<html lang="en">
<head>
<meta charset="utf-8">
<title>alpinleaf business card</title>
<link href="https://fonts.googleapis.com/css2?family=Work+Sans:wght@400;500;600;700&display=swap" rel="stylesheet">
<style>
  :root {
    --bg: #d4d4d4;
    --card-dark: #5c5c5e;
    --card-light: #ffffff;
    --ink: #4a4a4c;
    --ink-soft: #5a5a5c;
    --green: #7cc35a;
    --white: #ffffff;
  }
  * { box-sizing: border-box; margin: 0; padding: 0; }
  html, body { width: 1200px; height: 930px; overflow: hidden; }
  body {
    background: var(--bg);
    font-family: "Work Sans", Arial, sans-serif;
    position: relative;
  }
  .card {
    position: absolute;
    width: 520px;
    height: 300px;
    border-radius: 22px;
  }
  .card-back {
    left: 90px; top: 120px;
    background: var(--card-dark);
    display: flex; align-items: center; justify-content: center;
  }
  .card-front {
    left: 590px; top: 500px;
    background: var(--card-light);
  }
  .brand {
    display: flex; align-items: center; gap: 8px;
    font-weight: 700;
    letter-spacing: -0.5px;
  }
  .brand-square { display: block; background: var(--green); }
  .card-back .brand { color: var(--white); font-size: 56px; }
  .card-back .brand-square { width: 34px; height: 34px; }
  .card-front .brand {
    position: absolute; right: 36px; top: 34px;
    color: var(--ink); font-size: 40px;
  }
  .card-front .brand-square { width: 24px; height: 24px; }
  .holder-role {
    position: absolute; left: 34px; top: 112px;
    color: var(--green); font-weight: 600; font-size: 16px;
    letter-spacing: 0.8px; text-transform: uppercase;
    line-height: 20px;
  }
  .divider {
    position: absolute; left: 130px; right: 30px; top: 125px;
    height: 1px; background: var(--green);
  }
  .address {
    position: absolute; left: 56px; top: 150px;
    color: var(--ink-soft); font-size: 13.5px; line-height: 19px;
  }
  .contacts {
    position: absolute; left: 56px; top: 196px;
    list-style: none;
    color: var(--ink-soft); font-size: 13.5px; line-height: 20px;
  }
  .contacts li { display: flex; align-items: center; gap: 7px; }
  .contacts svg { width: 10px; height: 10px; flex: none; }
  .contacts .web { font-size: 15.5px; font-weight: 600; color: var(--ink); margin-top: 2px; }
  .web-accent { color: var(--green); }
</style>
</head>
<body>
  <section class="card card-back" aria-label="Card back">
    <div class="brand"><span class="brand-square"></span><span>alpinleaf</span></div>
  </section>

  <section class="card card-front" aria-label="Card front">
    <div class="brand"><span class="brand-square"></span><span>alpinleaf</span></div>
    <p class="holder-role">Director</p>
    <div class="divider"></div>
    <p class="address">42 Larchmont Lane,<br>Fernvale, 4410</p>
    <ul class="contacts">
      <li>
        <svg viewBox="0 0 10 10"><path d="M2 1 L4 1 L4.5 3 L3.3 3.8 Q4.3 5.8 6.2 6.7 L7 5.5 L9 6 L9 8 Q8.5 9 7.5 9 Q1 8 1 2.5 Q1 1.5 2 1Z" fill="#7cc35a"/></svg>
        <span>+41 (0) 70 555 01 23</span>
      </li>
      <li>
        <svg viewBox="0 0 10 10"><rect x="2.5" y="0.5" width="5" height="9" rx="1" fill="none" stroke="#7cc35a" stroke-width="1.2"/></svg>
        <span>+44 7700 90 01 24</span>
      </li>
      <li>
        <svg viewBox="0 0 10 10"><rect x="0.6" y="2" width="8.8" height="6" fill="none" stroke="#7cc35a" stroke-width="1.1"/><path d="M0.6 2 L5 5.5 L9.4 2" fill="none" stroke="#7cc35a" stroke-width="1.1"/></svg>
        <span>office@alpinleaf.net</span>
      </li>
      <li class="web">
        <svg viewBox="0 0 10 10"><circle cx="5" cy="5" r="4.3" fill="none" stroke="#7cc35a" stroke-width="1.1"/><path d="M0.7 5 H9.3 M5 0.7 Q2.5 5 5 9.3 M5 0.7 Q7.5 5 5 9.3" fill="none" stroke="#7cc35a" stroke-width="0.9"/></svg>
        <span>www.<span class="web-accent">alpinleaf</span>.net</span>
      </li>
    </ul>
  </section>
</body>
</html>
```